1 Page for Computer Repair Website

Looking for a 1 page website with a design that compliments the business card and pamphlet that have already been made (attached files). It should look business professional and easy to read. Email and phone number should be somewhere near the top of the website, visible when the page loads. I don't want any forms for people to mess with. No "Contact Us" form or entering in email for newsletter. Customers will just be looking at this site to confirm we are professionals and have our business in order.

Target Market(s)

Home and small business

Industry/Entity Type

Computer Repair

Coding

Coded - Design and coding required

Number of Pages Required

1 page

Font styles to use
Other font styles liked:
• Helvetica variations used in pamphlet and card

Colors
0455a3
cfdeed
85abd2
3276b5
85cae6
ffffff

Requirements
Must have
• Compliment the pamphlet and business card in color choices and font use. Pleasing to the eye and easy to read through categories and text.
Should not have
• Forms. No "enter name and email here" or anything of the sort.

```html
<!DOCTYPE html>
<html lang="en">
<head>
<meta charset="utf-8">
<title>ByteWell Computer Services</title>
<link href="https://fonts.googleapis.com/css2?family=Open+Sans:wght@400;600;700&family=Raleway:wght@400;500;600&display=swap" rel="stylesheet">
<style>
:root{
  --navy:#0455a3;
  --navy-dark:#03407c;
  --mid:#3276b5;
  --soft:#85abd2;
  --sky:#85cae6;
  --pale:#cfdeed;
  --white:#ffffff;
  --ink:#4a4f57;
  --muted:#8a9099;
  --line:#e3e8ee;
}
*{box-sizing:border-box;margin:0;padding:0}
html,body{width:1200px;height:2244px;overflow:hidden}
body{font-family:"Open Sans",Arial,sans-serif;color:var(--ink);background:var(--white);font-size:13px}
.page{width:1200px;height:2244px;position:relative}

/* header */
.site-header{height:112px;display:flex;justify-content:space-between;align-items:center;padding:0 60px}
.brand{display:flex;flex-direction:column;line-height:1}
.brand-name{font-weight:700;font-size:40px;color:var(--navy);letter-spacing:1px}
.brand-sub{font-weight:700;font-size:13px;color:var(--navy);letter-spacing:1px;margin-top:4px}
.quick-contact{text-align:right;line-height:1.5}
.quick-contact .label{color:var(--mid);font-size:15px;font-weight:600}
.quick-contact .phone{color:var(--navy);font-size:19px;font-weight:700;display:flex;gap:8px;align-items:center;justify-content:flex-end}
.quick-contact .email{color:var(--muted);font-size:12px;display:flex;gap:8px;align-items:center;justify-content:flex-end}

/* nav */
.main-nav{height:22px;background:linear-gradient(var(--sky),var(--soft));display:flex;padding-left:190px}
.main-nav a{color:var(--white);text-decoration:none;font-size:12px;font-weight:600;padding:0 26px;line-height:22px}
.main-nav a.active{background:var(--mid)}

/* hero */
.hero{position:relative;height:466px}
.hero-photo{position:absolute;inset:0;background:linear-gradient(100deg,#8fb0cf 0%,#c9d6e2 40%,#5d7d99 70%,#2f4c66 100%)}
.hero-caption{position:absolute;left:150px;top:150px;width:420px;background:rgba(20,40,70,.72);color:var(--white);padding:22px 26px}
.hero-caption h1{font-family:"Raleway",sans-serif;font-weight:500;font-size:36px;line-height:1.15}
.hero-caption h2{font-family:"Raleway",sans-serif;font-weight:400;font-size:22px;margin:4px 0 10px}
.hero-caption p{font-size:12px;line-height:1.5;opacity:.9}
.hero-dots{position:absolute;bottom:14px;left:50%;transform:translateX(-50%);display:flex;gap:8px}
.hero-dots span{width:14px;height:14px;border-radius:50%;background:var(--white);opacity:.7}
.hero-dots span.on{background:var(--mid);opacity:1}

/* about */
.about{height:410px;background:#f7f8fa;text-align:center;padding:70px 150px 0}
.section-title{font-family:"Raleway",sans-serif;font-weight:500;color:var(--navy);font-size:34px;letter-spacing:1px}
.rule{width:560px;height:1px;background:var(--soft);margin:6px auto 20px}
.about p{font-size:12px;line-height:1.9;color:var(--muted);margin-bottom:16px}
.btn{display:inline-block;background:var(--navy);color:var(--white);font-size:13px;padding:9px 22px;border-radius:2px;margin-top:22px}

/* services */
.services{height:590px;text-align:center;padding-top:66px}
.services .section-title{color:var(--ink);font-size:30px}
.service-grid{display:grid;grid-template-columns:repeat(4,180px);column-gap:60px;row-gap:42px;justify-content:center;margin-top:20px}
.service{display:flex;flex-direction:column;align-items:center}
.service .icon{width:80px;height:80px;border-radius:50%;border:2px solid var(--line);display:flex;align-items:center;justify-content:center;margin-bottom:12px}
.service h3{font-size:15px;font-weight:600;color:var(--ink);line-height:1.25;min-height:38px;display:flex;align-items:center}
.service p{font-size:11px;line-height:1.6;color:var(--muted);margin:4px 0 8px;min-height:35px}
.service .more{font-size:11px;font-weight:700;color:var(--navy)}

/* why */
.why{height:244px;background:var(--pale);position:relative;padding:48px 0 0 200px}
.why h2{font-family:"Raleway",sans-serif;font-weight:500;color:var(--navy);font-size:32px}
.why .intro{width:440px;font-size:11px;line-height:1.6;color:var(--ink);margin:8px 0 12px}
.checklist{list-style:none}
.checklist li{font-size:11px;line-height:1.9;display:flex;gap:8px;align-items:center}
.why-photo{position:absolute;right:190px;top:0;width:320px;height:244px;background:linear-gradient(120deg,#e9eef4,#b9c6d4 55%,#38404b)}

/* footer */
.site-footer{height:378px;background:var(--navy);color:var(--white);padding:66px 0 0 190px;display:grid;grid-template-columns:180px 180px 180px 260px;column-gap:40px;align-content:start}
.site-footer h4{font-size:15px;font-weight:600;margin-bottom:12px;letter-spacing:.5px}
.site-footer li{list-style:none;font-size:12px;line-height:1.9;color:var(--pale)}
.copyright{position:absolute;left:0;bottom:0;width:1200px;height:44px;background:var(--navy-dark);color:var(--soft);font-size:11px;line-height:44px;padding-left:190px}
</style>
</head>
<body>
<div class="page">

<header class="site-header">
  <div class="brand">
    <span class="brand-name">ByteWell</span>
    <span class="brand-sub">Computer Services</span>
  </div>
  <div class="quick-contact">
    <div class="label">Quick Contact</div>
    <div class="phone">
      <svg width="16" height="16" viewBox="0 0 24 24"><path fill="#3276b5" d="M6.6 10.8a15 15 0 0 0 6.6 6.6l2.2-2.2a1 1 0 0 1 1-.25 11.4 11.4 0 0 0 3.6.6 1 1 0 0 1 1 1V20a1 1 0 0 1-1 1A17 17 0 0 1 3 4a1 1 0 0 1 1-1h3.5a1 1 0 0 1 1 1c0 1.25.2 2.45.6 3.6a1 1 0 0 1-.25 1z"/></svg>
      555.014.2290
    </div>
    <div class="email">
      <svg width="14" height="11" viewBox="0 0 14 11"><rect x=".5" y=".5" width="13" height="10" fill="none" stroke="#3276b5"/><path d="M.5 .5l6.5 5 6.5-5" fill="none" stroke="#3276b5"/></svg>
      info@bytewell.example
    </div>
  </div>
</header>

<nav class="main-nav">
  <a class="active">Home</a><a>About Us</a><a>Our Services</a><a>Support</a><a>Testimonials</a><a>FAQ</a><a>Contact</a>
</nav>

<section class="hero">
  <div class="hero-photo" role="img" aria-label="Technician repairing the inside of a desktop computer"></div>
  <div class="hero-caption">
    <h1>PC &amp; Laptop Repair</h1>
    <h2>Cum sociis natoque penatibus</h2>
    <p>Fast, friendly repairs for home and small business computers, done right the first time.</p>
  </div>
  <div class="hero-dots"><span></span><span class="on"></span><span></span><span></span></div>
</section>

<section class="about">
  <h2 class="section-title">ABOUT OUR COMPANY</h2>
  <div class="rule"></div>
  <p>We are a local computer repair team serving homes and small businesses. Our certified technicians diagnose problems quickly, explain every option in plain language and fix your machine at a fair price. We repair desktops, laptops and Macs, remove viruses, recover lost files and upgrade older systems so they run like new again.</p>
  <p>Every job comes with a clear quote before work begins and a warranty once it is done. We keep your data private, return your computer on time and stay available afterwards for any questions you may have about your system.</p>
  <span class="btn">Hire Us Now</span>
</section>

<section class="services">
  <h2 class="section-title">Services We Provide</h2>
  <div class="rule" style="width:380px"></div>
  <div class="service-grid">
    <div class="service">
      <div class="icon"><svg width="34" height="38" viewBox="0 0 24 26"><path d="M12 1 2 5v7c0 6 4.5 11 10 13 5.5-2 10-7 10-13V5z" fill="#0455a3"/></svg></div>
      <h3>Malware/Virus Removal</h3>
      <p>Full virus and spyware cleanup with protection added.</p>
      <span class="more">LEARN MORE</span>
    </div>
    <div class="service">
      <div class="icon"><svg width="38" height="34" viewBox="0 0 26 22"><rect x="1" y="1" width="24" height="15" rx="1" fill="none" stroke="#0455a3" stroke-width="2"/><rect x="9" y="18" width="8" height="3" fill="#0455a3"/></svg></div>
      <h3>PC/Mac/Laptop<br>Hardware Repair</h3>
      <p>Screens, keyboards, drives and power faults fixed fast.</p>
      <span class="more">LEARN MORE</span>
    </div>
    <div class="service">
      <div class="icon"><svg width="34" height="34" viewBox="0 0 24 24"><path d="M12 2v13M7 10l5 5 5-5" fill="none" stroke="#0455a3" stroke-width="2.4"/><path d="M3 17v4h18v-4" fill="none" stroke="#0455a3" stroke-width="2.4"/></svg></div>
      <h3>Upgrades</h3>
      <p>More memory, faster storage and new parts for longer life.</p>
      <span class="more">LEARN MORE</span>
    </div>
    <div class="service">
      <div class="icon"><svg width="34" height="34" viewBox="0 0 24 24"><rect x="2" y="2" width="12" height="14" fill="none" stroke="#0455a3" stroke-width="2"/><rect x="10" y="8" width="12" height="14" fill="#0455a3"/></svg></div>
      <h3>Data Migration</h3>
      <p>Move files, settings and programs to your new computer.</p>
      <span class="more">LEARN MORE</span>
    </div>
    <div class="service">
      <div class="icon"><svg width="34" height="34" viewBox="0 0 24 24"><circle cx="12" cy="12" r="9" fill="none" stroke="#0455a3" stroke-width="3"/><circle cx="12" cy="12" r="4" fill="none" stroke="#0455a3" stroke-width="2"/></svg></div>
      <h3>Data Rescue</h3>
      <p>Recover photos and documents from failed drives.</p>
      <span class="more">LEARN MORE</span>
    </div>
    <div class="service">
      <div class="icon"><svg width="34" height="34" viewBox="0 0 24 24"><rect x="6" y="6" width="12" height="12" fill="#0455a3"/><path d="M9 2v4M15 2v4M9 18v4M15 18v4M2 9h4M2 15h4M18 9h4M18 15h4" stroke="#0455a3" stroke-width="2"/></svg></div>
      <h3>Tune-Ups</h3>
      <p>Speed up slow machines with cleanup and full checks.</p>
      <span class="more">LEARN MORE</span>
    </div>
    <div class="service">
      <div class="icon"><svg width="34" height="34" viewBox="0 0 24 24"><path d="M3 21l9-9M14 3a5 5 0 0 0-1.5 6L3 18.5 5.5 21 15 11.5A5 5 0 0 0 21 10l-3 1-2-2 1-3z" fill="#0455a3"/></svg></div>
      <h3>In-Home Installation</h3>
      <p>We set up computers, printers and networks at home.</p>
      <span class="more">LEARN MORE</span>
    </div>
    <div class="service">
      <div class="icon"><svg width="34" height="34" viewBox="0 0 24 24"><circle cx="12" cy="12" r="6" fill="none" stroke="#0455a3" stroke-width="4"/><path d="M12 1v5M12 18v5M1 12h5M18 12h5M4 4l3.5 3.5M16.5 16.5 20 20M4 20l3.5-3.5M16.5 7.5 20 4" stroke="#0455a3" stroke-width="3"/></svg></div>
      <h3>Remote Support</h3>
      <p>Quick help over a secure link without leaving home.</p>
      <span class="more">LEARN MORE</span>
    </div>
  </div>
</section>

<section class="why">
  <h2>Why Choose Us</h2>
  <p class="intro">Honest pricing, skilled technicians and fast turnaround. We treat every computer as if it were our own and keep you informed from the first call to the final fix.</p>
  <ul class="checklist">
    <li><svg width="12" height="12" viewBox="0 0 12 12"><circle cx="6" cy="6" r="6" fill="#0455a3"/><path d="M3 6l2 2 4-4" stroke="#fff" stroke-width="1.5" fill="none"/></svg>Certified technicians with years of hands on experience</li>
    <li><svg width="12" height="12" viewBox="0 0 12 12"><circle cx="6" cy="6" r="6" fill="#0455a3"/><path d="M3 6l2 2 4-4" stroke="#fff" stroke-width="1.5" fill="none"/></svg>Clear quotes before work starts and no hidden fees</li>
    <li><svg width="12" height="12" viewBox="0 0 12 12"><circle cx="6" cy="6" r="6" fill="#0455a3"/><path d="M3 6l2 2 4-4" stroke="#fff" stroke-width="1.5" fill="none"/></svg>Most repairs finished within one to two days</li>
    <li><svg width="12" height="12" viewBox="0 0 12 12"><circle cx="6" cy="6" r="6" fill="#0455a3"/><path d="M3 6l2 2 4-4" stroke="#fff" stroke-width="1.5" fill="none"/></svg>Warranty on all parts and labour we provide</li>
  </ul>
  <div class="why-photo" role="img" aria-label="Technician pointing at an open computer tower"></div>
</section>

<footer class="site-footer">
  <div><h4>COMPANY</h4><ul><li>Company</li><li>Why Choose Us</li><li>Our Team</li><li>Privacy Policy</li></ul></div>
  <div><h4>SERVICES</h4><ul><li>Malware/Virus Removal</li><li>Upgrades</li><li>Data Migration</li><li>Data Rescue</li><li>Tune-Ups</li></ul></div>
  <div><h4>RESOURCES</h4><ul><li>Support</li><li>Testimonials</li><li>FAQ</li><li>Contact Us</li></ul></div>
  <div><h4>CONTACT INFO</h4><ul><li>1420 Maple Street, Suite 210</li><li>Riverton, Brookfield</li><li>Phone: 555.014.2290</li><li>Email: info@bytewell.example</li></ul></div>
  <div class="copyright">© 2024 ByteWell Computer Services. All rights reserved.</div>
</footer>

</div>
</body>
</html>
```